Quillbrookes websites redesign

Www.quill-brookes.com needs to be redesigned along with updations. The incremental material will be provided for the updations. We are looking for complete redesign of the pages with the new content. The complete write up will be provided soon

Target Market(s)

Global

Coding

Coded - Design and coding required

Number of Pages Required

5+ page

Requirements
Must have
• A clean and slick design for the Consulting.
Should not have
• Too many pictures which reduces the speed of the site

```html
<!DOCTYPE html>
<html lang="en">
<head>
<meta charset="utf-8">
<title>Quillbrookes Consultancy</title>
<link href="https://fonts.googleapis.com/css2?family=Raleway:wght@400;500;600&family=Open+Sans:wght@400;600&display=swap" rel="stylesheet">
<style>
:root{
  --maroon:#6b1f22;
  --footer:#6a2424;
  --blue:#2b94c9;
  --blue-dark:#1f7fb5;
  --nav-active:#1b6fae;
  --text:#666;
  --ink:#333;
  --white:#fff;
}
*{margin:0;padding:0;box-sizing:border-box}
html,body{width:766px;height:1200px;overflow:hidden;background:var(--white)}
body{position:relative;font-family:"Open Sans",sans-serif;color:var(--text)}
.site-header{position:absolute;top:0;left:0;width:766px;height:66px;background:var(--white)}
.brand{position:absolute;left:96px;top:22px;display:flex;align-items:center;gap:7px;font-family:"Raleway",sans-serif;font-size:19px;font-weight:500;color:var(--maroon)}
.brand .mark{width:14px;height:14px;border-radius:50%;background:var(--blue)}
.main-nav{position:absolute;top:31px;left:271px;display:flex;gap:21px;font-family:"Raleway",sans-serif;font-size:9.5px;font-weight:500;color:#333;letter-spacing:.2px}
.main-nav .active{color:var(--nav-active);position:relative}
.main-nav .active::after{content:"";position:absolute;left:-3px;right:-3px;top:31px;height:2px;background:var(--nav-active)}
.hero{position:absolute;top:66px;left:0;width:766px;height:316px;background:linear-gradient(160deg,#5e7fa6 0%,#a9bdd3 40%,#6d8fb5 70%,#3c5f8c 100%)}
.hero-title{position:absolute;top:96px;width:100%;text-align:center;font-family:"Raleway",sans-serif;font-weight:600;color:var(--white);font-size:24px;line-height:34px;text-shadow:0 1px 3px rgba(0,0,0,.35)}
.hero-title .big{font-size:28px}
.btn-hero{position:absolute;left:340px;top:170px;width:85px;height:26px;border:1px solid var(--white);background:var(--maroon);color:var(--white);font-size:10.5px;display:flex;align-items:center;justify-content:center}
.slider-dots{position:absolute;top:290px;left:359px;display:flex;gap:3px}
.slider-dots span{width:11px;height:11px;border-radius:50%;background:var(--white)}
.slider-dots .on{background:#e8772e;border:2px solid var(--white)}
.intro{position:absolute;top:382px;left:0;width:766px;height:216px;text-align:center}
.world-map{position:absolute;left:190px;top:70px;width:390px;height:140px;background:radial-gradient(ellipse,#ececec 40%,rgba(255,255,255,0) 72%)}
.intro h1{position:relative;margin-top:34px;font-family:"Raleway",sans-serif;font-weight:400;font-size:24px;color:var(--maroon)}
.intro h2{position:relative;font-family:"Raleway",sans-serif;font-weight:400;font-size:14.5px;color:var(--maroon);margin-top:3px}
.intro p{position:relative;width:565px;margin:12px auto 0;font-size:7.8px;line-height:12.4px;color:var(--text)}
.intro p + p{margin-top:9px}
.services{position:absolute;top:598px;left:0;width:766px;height:240px;background:linear-gradient(135deg,var(--blue) 0%,#3aa6d6 50%,var(--blue-dark) 100%)}
.notch{position:absolute;left:313px;top:0}
.notch-dot{position:absolute;left:374px;top:598px;width:18px;height:18px;border-radius:50%;background:var(--blue)}
.service{position:absolute;top:50px;width:200px;text-align:center;color:var(--white)}
.service svg{display:block;margin:0 auto;height:48px}
.service h3{margin-top:22px;font-family:"Raleway",sans-serif;font-weight:500;font-size:13px;letter-spacing:.3px}
.service p{margin-top:7px;font-size:7.3px;line-height:10.8px;color:#e4f3fb}
.btn-outline{display:inline-block;margin-top:14px;width:69px;height:21px;line-height:19px;border:1.5px solid var(--white);font-size:8px;color:var(--white)}
.blogs{position:absolute;top:838px;left:0;width:766px;height:279px}
.blogs h2{position:absolute;top:30px;width:100%;text-align:center;font-family:"Raleway",sans-serif;font-weight:400;font-size:19.5px;color:var(--blue)}
.post{position:absolute;top:72px;width:179px}
.post-photo{position:relative;height:93px;background:linear-gradient(120deg,#c9d7e3,#eef2f6 55%,#a9b9c8)}
.post-date{position:absolute;left:0;bottom:0;width:96px;height:20px;line-height:20px;padding-left:10px;background:rgba(43,148,201,.88);color:var(--white);font-size:9px}
.post h4{margin-top:9px;padding-left:2px;font-family:"Raleway",sans-serif;font-weight:500;font-size:10.5px;color:var(--maroon)}
.post p{margin-top:3px;padding-left:2px;font-size:7px;line-height:10px;color:#555}
.post a{display:block;margin-top:4px;padding-left:2px;font-size:7.5px;color:var(--blue);text-decoration:none}
.site-footer{position:absolute;top:1117px;left:0;width:766px;height:83px;background:var(--footer);color:var(--white)}
.footer-nav{position:absolute;left:94px;top:24px;display:flex;gap:14px;font-family:"Raleway",sans-serif;font-size:8.5px;font-weight:500}
.copyright{position:absolute;left:94px;top:45px;font-size:7px;color:#e6d4d4}
.social{position:absolute;left:472px;top:23px;display:flex;gap:2px}
.social span{width:15px;height:15px;border-radius:50%;border:1px solid var(--white)}
.footer-brand{position:absolute;left:557px;top:22px;display:flex;align-items:center;gap:7px;font-family:"Raleway",sans-serif;font-size:17px;font-weight:500;color:#d9c3c3}
.footer-brand .mark{width:14px;height:14px;border-radius:50%;background:#d9c3c3}
</style>
</head>
<body>
<header class="site-header">
  <div class="brand"><span class="mark"></span>Quillbrookes</div>
  <nav class="main-nav">
    <span class="active">HOME</span><span>FOUNDER</span><span>CONSULTANCY</span><span>SYSTEM</span><span>CASE STUDIES</span><span>CONTACT</span>
  </nav>
</header>

<section class="hero" role="img" aria-label="Photo of a bank building facade with columns and glass tower">
  <div class="hero-title">QUILLBROOKES TRADE AND INVESTMENT<br><span class="big">CONSULTANCY SERVICE</span></div>
  <div class="btn-hero">Read More</div>
  <div class="slider-dots"><span class="on"></span><span></span><span></span><span></span></div>
</section>

<section class="intro">
  <div class="world-map" role="img" aria-label="Faint world map background"></div>
  <h1>Quillbrookes Consultancy Limited</h1>
  <h2>Mauris vel lacus vitae felis vestibulum volutpat</h2>
  <p>We capitalizes on synergies arising from trade and investment linkages between countries and knowledge of traditional and non-traditional pools of liquidity to provide consultancy services to Emerging country banks, Corporates and SMEs.</p>
  <p>The Consultancy provides bank neutral views to Corporates and SMEs in Asian emerging markets and helps in improving financial structure and efficient use of funds. Our endeavor is to provide a distinct bottom line advantage to our clients. The primary focus is in regionalisation of the banking relationship across the globe, providing structured finance solutions and off balance sheet solutions.</p>
</section>

<section class="services">
  <svg class="notch" width="140" height="30" viewBox="0 0 140 30"><path d="M0 0 H140 C110 0 100 30 70 30 C40 30 30 0 0 0Z" fill="#fff"/></svg>
  <div class="service" style="left:90px">
    <svg viewBox="0 0 60 48" width="60"><circle cx="36" cy="18" r="14" fill="none" stroke="#fff" stroke-width="4"/><text x="36" y="25" font-size="18" font-family="Open Sans" font-weight="600" fill="#fff" text-anchor="middle">$</text><path d="M4 32h10l10 4h12l-2 4H22l14 2 18-8 2 3-20 11H4z" fill="#fff"/></svg>
    <h3>FINANCIAL SERVICE</h3>
    <p>Mauris vel lacus vitae felis vestibulum volutpat<br>Eeu imperdiet ac nisl Cum sociis natoque<br>penatibus et magnis dis parturi</p>
    <span class="btn-outline">Read More</span>
  </div>
  <div class="service" style="left:286px">
    <svg viewBox="0 0 60 48" width="60"><circle cx="24" cy="12" r="9" fill="#fff"/><path d="M6 46c0-14 8-20 18-20s18 6 18 20z" fill="#fff"/><path d="M22 26l2 12 2-12z" fill="#2b94c9"/><rect x="38" y="2" width="20" height="13" rx="2" fill="none" stroke="#fff" stroke-width="2"/><path d="M42 15l-3 5 7-5" fill="#fff"/></svg>
    <h3>CONSULTANCY</h3>
    <p>Mauris vel lacus vitae felis vestibulum volutpat<br>Eeu imperdiet ac nisl Cum sociis natoque<br>penatibus et magnis dis parturi</p>
    <span class="btn-outline">Read More</span>
  </div>
  <div class="service" style="left:486px">
    <svg viewBox="0 0 60 48" width="60"><path d="M18 8 30 2 42 8z" fill="#fff"/><rect x="19" y="10" width="22" height="2" fill="#fff"/><rect x="21" y="13" width="3" height="9" fill="#fff"/><rect x="28.5" y="13" width="3" height="9" fill="#fff"/><rect x="36" y="13" width="3" height="9" fill="#fff"/><rect x="19" y="22" width="22" height="2" fill="#fff"/><path d="M30 25v6M10 31h40M10 31v4M30 31v4M50 31v4" stroke="#fff" stroke-width="1.4" stroke-dasharray="2 1.5"/><circle cx="10" cy="38" r="3" fill="#fff"/><circle cx="30" cy="38" r="3" fill="#fff"/><circle cx="50" cy="38" r="3" fill="#fff"/><path d="M4 48c0-5 3-7 6-7s6 2 6 7zM24 48c0-5 3-7 6-7s6 2 6 7zM44 48c0-5 3-7 6-7s6 2 6 7z" fill="#fff"/></svg>
    <h3>BANKING RELATIONSHIP</h3>
    <p>Mauris vel lacus vitae felis vestibulum volutpat<br>eu imperdiet ac nisl Cum sociis natoque<br>penatibus et magnis dis parturi</p>
    <span class="btn-outline">Read More</span>
  </div>
</section>
<div class="notch-dot"></div>

<section class="blogs">
  <h2>Latest Blogs</h2>
  <article class="post" style="left:102px">
    <div class="post-photo" role="img" aria-label="Photo of business colleagues in a meeting"><span class="post-date">26 Dec, 2015</span></div>
    <h4>Praesent elementum elit</h4>
    <p>tellus Curabitur metus ipsum luctus eu male suada ut tincidunt sed diam Donec quis mi sed magna hendrerit Suspendisse</p>
    <a href="#">Learn More</a>
  </article>
  <article class="post" style="left:300px">
    <div class="post-photo" role="img" aria-label="Photo of a team presentation in an office"><span class="post-date">29 Dec, 2015</span></div>
    <h4>Nulla rhoncus dictum metus</h4>
    <p>tellus Curabitur metus ipsum luctus eu male suada ut tincidunt sed diam Donec quis mi sed magna hendrerit Suspendisse</p>
    <a href="#">Learn More</a>
  </article>
  <article class="post" style="left:498px">
    <div class="post-photo" role="img" aria-label="Photo of two people reviewing documents"><span class="post-date">30 Dec, 2015</span></div>
    <h4>Suspendisse risus nibh</h4>
    <p>tellus Curabitur metus ipsum luctus eu male suada ut tincidunt sed diam Donec quis mi sed magna hendrerit Suspendisse</p>
    <a href="#">Learn More</a>
  </article>
</section>

<footer class="site-footer">
  <nav class="footer-nav"><span>HOME</span><span>FOUNDER</span><span>CONSULTANCY</span><span>SYSTEM</span><span>CASE STUDIES</span><span>CONTACT</span></nav>
  <div class="copyright">© 2016 Company Name &nbsp;All right reserved &nbsp;Term of Use</div>
  <div class="social"><span></span><span></span><span></span><span></span></div>
  <div class="footer-brand"><span class="mark"></span>Quillbrookes</div>
</footer>
</body>
</html>
```